Cash Balance Retirement Plan Services Page

We are looking to have a services/landing page created for one of our offerings. The goal of the page is to explain a relatively complex service (advanced retirement plan) by highlighting the benefits and uses for the plan such that it tells a story that encourages individuals and businesses that would benefit from the plans to reach out.

The page will be used both as a landing page (though secondarily) and as a page that many of our partners will show to their clients in order to generate interest. We help other people closes these deals so we want it to handle both.

Overall, we would want the page to incorporate the following sections/areas.
1. Headline and a place for a video at the top
2. Explanation of what a cash balance plan is (a paragraph or two)
3. These five benefits: These are the 7 we usually use, but only include five at a time so only need room for five.
a. Highest Tax Deductible Contributions Allowed
b. Significantly reduce your taxes
c. Potential Negative “Net Cost”
d. Owner & Executive Weighted Benefits
e. Retain and Attract Top Talen
f. Catch Up On decades of low retirement savings in a matter of years
g. Potential for life time income
4. A section comparing the contribution limits allowed for each plan type (Please see attached image as an example).
5. A place for a table of contribution amounts (This will just be an image. Also, attached).
6. A place for a compare table
6. Who should consider such a plan
7. Occasional banners for call to actions
8. FAQ

Our primary audience for this project are successful small business owners with a particular focus on medical professionals (doctors, chiropractors, dentists, plastic surgeons, etc.). In generally, they will be between 45 and 65 years old and earn $150k or more.

Because we work a lot with financial, business strategy, and insurance based products that require a significant investment by the client trust, professionalism, and sophistication are important attributes we wish to portray in the design of the page. Our preferred colors are blue or green. Though we are still working on figuring out the color scheme so your input as a designer is welcomed as your creativity can help us communicate the attributes we seek to embody for our clients.

In the attached document, I have included some additional information about the service itself if it helps to have some context, as well as a more flushed out outline of the details above.

Importantly, I am not a marketer so any creative input is always welcome if there is a best practice we are not incorporating in either our design requests or outline.

Here is the URL for our current page: https://www.brightvaleadvisors.com/physicianplan

Please don't let this page be your muse. We're trying to get away from it for a reason :) But it still will hopefully provide some helpful information, copy examples, and context.

Additionally, please don't feel like you need to read the full cash balance explanation. That's only if context will be helpful.

We are also going through a rebranding so please don't rely on the colors from the BrightValeAdvisors logo you may see on the website. I've attached two sample logos for the rebrand for context.

```html
<!DOCTYPE html>
<html lang="en">
<head>
<meta charset="utf-8">
<title>BrightVale – Cash Balance Plan for Physicians</title>
<link rel="stylesheet" href="https://fonts.googleapis.com/css2?family=Poppins:wght@300;400;500;600;700&family=Oswald:wght@500&family=Arimo:wght@400;700&display=swap">
<style>
:root{
  --navy:#0b4a86;
  --blue:#14609f;
  --bright:#1d7ac2;
  --sky:#dcedf8;
  --sky-2:#bcd9ea;
  --ink:#1b1b1b;
  --muted:#4a4a4a;
  --row-a:#c9d5ee;
  --row-b:#e5ebf6;
  --table-head:#0f3f8c;
  --white:#ffffff;
}
*{box-sizing:border-box;margin:0;padding:0}
html,body{width:1200px;height:5338px;overflow:hidden}
body{font-family:"Poppins",sans-serif;color:var(--ink);background:var(--white);position:relative}
.abs{position:absolute}
.accent{color:var(--bright);font-weight:400}

/* hero */
.hero{position:absolute;left:0;top:0;width:1200px;height:684px;
  background:radial-gradient(ellipse at 90% 30%,#2a7fc4 0%,transparent 45%),radial-gradient(ellipse at 10% 60%,#2a7fc4 0%,transparent 40%),linear-gradient(180deg,#1660a3,#0f5596)}
.hero-cut{position:absolute;left:0;bottom:-1px;width:1200px;height:120px}
.logo{position:absolute;left:110px;top:34px;font-weight:700;font-size:30px;color:var(--white);letter-spacing:.2px}
.nav{position:absolute;left:568px;top:46px;display:flex;gap:26px;font-size:13px;color:var(--white)}
.nav .active{border-bottom:2px solid var(--white);padding-bottom:4px}
.quote-btn{position:absolute;left:941px;top:35px;width:145px;height:42px;border-radius:21px;background:var(--white);color:var(--navy);font-size:13px;font-weight:700;display:flex;align-items:center;justify-content:center}
.hero-title{position:absolute;left:0;top:134px;width:1200px;text-align:center;color:var(--white);font-weight:700;font-size:38px;line-height:47px}
.video{position:absolute;left:234px;top:267px;width:732px;height:419px;border-radius:16px;overflow:hidden;
  background:linear-gradient(180deg,#5fa7d4,#3f8fc6)}
.video-art{position:absolute;inset:0;background:radial-gradient(ellipse at 50% 30%,#a9a9a9 0%,#8e8e8e 40%,transparent 62%),radial-gradient(ellipse at 50% 95%,#e9eef2 0%,transparent 30%)}
.video-head{position:absolute;left:0;top:42px;width:100%;text-align:center;font-family:"Oswald",sans-serif;color:var(--white);font-size:52px;line-height:64px}
.video-sub{position:absolute;left:0;top:118px;width:100%;text-align:center;font-family:"Oswald",sans-serif;color:var(--white);font-size:25px}
.play{position:absolute;left:341px;top:186px}

/* what is */
.what h2{position:absolute;left:110px;top:762px;font-size:36px;line-height:46px;font-weight:700}
.what h2 .accent{display:block;font-size:38px;font-weight:400}
.what p{position:absolute;left:110px;top:902px;width:462px;font-size:13px;line-height:25.7px;color:var(--muted);text-align:justify}
.photo{background:linear-gradient(160deg,#c9d3dc,#6f8aa3)}

/* benefits */
.benefits{position:absolute;left:0;top:1244px;width:1200px;height:860px;background:var(--sky)}
.sec-title{position:absolute;left:0;width:1200px;text-align:center;font-size:36px;font-weight:700}
.rule{position:absolute;left:515px;width:170px;height:2px;background:var(--blue)}
.hex{position:absolute;width:270px;height:270px}
.hex svg{position:absolute;inset:0}
.hex .icon{position:absolute;left:95px;top:44px;width:80px;height:80px}
.hex .label{position:absolute;left:40px;top:150px;width:190px;text-align:center;font-size:15px;line-height:26px;color:var(--muted)}
.hex.filled .label{color:var(--white)}

/* table */
.contrib-title{position:absolute;left:0;top:2178px;width:1200px;text-align:center;font-size:38px;line-height:52px;font-weight:700}
.contrib-title .accent{display:block;font-size:39px}
.limits{position:absolute;left:172px;top:2334px;width:854px;border-collapse:collapse;font-family:"Arimo",sans-serif;font-size:20px;box-shadow:0 3px 8px rgba(0,0,0,.25);border:3px solid #fff}
.limits th{background:var(--table-head);color:var(--white);text-align:left;vertical-align:top;padding:6px 10px;line-height:28px;font-weight:700;border-right:2px solid #fff;height:126px}
.limits td{padding:0 10px;height:39px;border-right:2px solid #fff;border-top:1px solid #fff}
.limits tr:nth-child(odd) td{background:var(--row-a)}
.limits tr:nth-child(even) td{background:var(--row-b)}
.limits td:nth-child(4){font-weight:700}
.savings-link{position:absolute;left:0;top:2686px;width:1200px;text-align:center;color:var(--blue);font-size:25px;font-weight:500}

/* chart */
.amounts{position:absolute;left:0;top:2803px;width:1200px;height:829px;background:linear-gradient(135deg,#0f5aa0,#0a4785 60%,#0d4f92)}
.amounts .sec-title{color:var(--white);top:90px;font-weight:400}
.amounts .sec-title b{font-weight:700}
.chart{position:absolute;left:286px;top:247px;width:628px;height:370px;background:var(--white);border-radius:6px}

/* who */
.who-photo{position:absolute;left:110px;top:3717px;width:462px;height:574px;border-radius:14px;background:linear-gradient(170deg,#f1f3f5,#c9d4de 60%,#9eb1c4)}
.who h2{position:absolute;left:618px;top:3712px;font-size:40px;line-height:50px;font-weight:700}
.who h2 .accent{display:block;font-size:40px}
.who .intro{position:absolute;left:618px;top:3868px;width:470px;font-size:13.5px;line-height:25.5px;color:var(--muted)}
.ticks{position:absolute;left:618px;top:3964px;width:480px;list-style:none;font-size:13.5px;line-height:25.5px;color:var(--muted)}
.ticks li{position:relative;padding-left:26px}
.ticks svg{position:absolute;left:0;top:7px}

/* faq */
.faq-title{position:absolute;left:0;top:4367px;width:1200px;text-align:center;font-size:38px;font-weight:700}
.faq{position:absolute;left:261px;width:678px;border-radius:10px;background:#e6f2fb;border:2px solid #cfe3f1;font-size:13px;color:var(--muted)}
.faq .q{position:absolute;left:28px;top:18px}
.faq .plus{position:absolute;right:16px;top:12px;width:30px;height:30px;border-radius:6px;background:var(--navy);color:#fff;font-size:15px;display:flex;align-items:center;justify-content:center;font-weight:600}
.faq.open{background:var(--navy);border-color:var(--navy);color:var(--white)}
.faq.open .q{font-weight:600}
.faq.open .plus{background:#d7e8f5;color:var(--navy)}
.faq.open p{position:absolute;left:28px;top:64px;width:620px;font-size:12px;line-height:26px;text-align:justify}

/* footer */
.footer{position:absolute;left:0;top:5052px;width:1200px;height:286px}
.footer .f-logo{position:absolute;left:0;top:70px;width:1200px;text-align:center;color:#fff;font-weight:700;font-size:34px}
.f-links{position:absolute;left:0;top:132px;width:1200px;text-align:center;color:#fff;font-size:13px;word-spacing:2px}
.f-links span{margin:0 12px}
.copy{position:absolute;left:0;top:226px;width:1200px;text-align:center;color:#fff;font-size:12px}
</style>
</head>
<body>

<header class="hero">
  <svg class="hero-cut" viewBox="0 0 1200 120" preserveAspectRatio="none"><path d="M0 0 L0 120 L1200 120 L1200 95 C800 110 300 80 0 0Z" fill="#fff"/></svg>
  <div class="logo">BrightVale</div>
  <nav class="nav"><span class="active">Home</span><span>About us</span><span>Services</span><span>Blog</span><span>Contact us</span></nav>
  <div class="quote-btn">GET A QUOTE</div>
  <h1 class="hero-title">Are you healthy enough that you are<br>at risk of outliving your retirement savings?</h1>
  <div class="video">
    <div class="video-art" role="img" aria-label="Video thumbnail illustration: cartoon doctor in a white coat beneath a grey speech bubble with question marks"></div>
    <div class="video-head">Doctors,</div>
    <div class="video-sub">Are you healthy and worried about out living your retirement savings?</div>
    <svg class="play" width="50" height="50" viewBox="0 0 50 50"><circle cx="25" cy="25" r="25" fill="#0c4f8e"/><path d="M20 15 L35 25 L20 35Z" fill="#fff"/></svg>
  </div>
</header>

<section class="what">
  <h2>What is a <span class="accent">Cash-Balance Plan</span></h2>
  <p>A cash balance plan is a retirement plan specifically for small business owners, doctors, lawyers, and other high-income professionals. It allows for the highest tax-deductible contribution limits in the market, and the older you get, the higher those limits go. You then get an option for guaranteed income for life or a one time, lump payout. They are a hybrid plan that combines a the benefits of a defined benefit plan (Pensions) with those of a defined contribution plan (IRA, 401k, etc.). They are often not dependent on the stock market, which is a huge boon.</p>
  <svg class="abs" style="left:630px;top:740px" width="470" height="470" viewBox="0 0 470 470">
    <circle cx="141" cy="321" r="133" fill="#c6dfed"/>
    <circle cx="324" cy="68" r="58" fill="#c6dfed"/>
    <rect x="257" y="114" width="110" height="120" fill="#2e7cbf"/>
  </svg>
  <div class="abs photo" style="left:655px;top:765px;width:226px;height:234px" role="img" aria-label="Photo of a smiling senior doctor with a stethoscope"></div>
  <div class="abs photo" style="left:705px;top:1005px;width:145px;height:83px;background:linear-gradient(160deg,#5b9bd0,#1f5f9a)" role="img" aria-label="Photo of surgeons in blue scrubs"></div>
  <div class="abs photo" style="left:854px;top:927px;width:226px;height:230px;background:linear-gradient(160deg,#e3e8ec,#4f85c4)" role="img" aria-label="Photo of a smiling doctor in blue scrubs"></div>
</section>

<section class="benefits">
  <h2 class="sec-title" style="top:92px">Our <span class="accent">Benefits</span></h2>
  <div class="rule" style="top:172px"></div>

  <div class="hex" style="left:139px;top:190px">
    <svg viewBox="0 0 270 270"><polygon points="135,8 250,72 250,198 135,262 20,198 20,72" fill="#fff" stroke="#0b4a86" stroke-width="2.5" stroke-linejoin="round"/></svg>
    <svg class="icon" viewBox="0 0 80 80"><path d="M30 6h20l-6 14h-8z" fill="#0b4a86"/><path d="M36 22h8c18 10 26 28 24 42-2 10-12 12-28 12S14 74 12 64C10 50 18 32 36 22z" fill="#0b4a86"/><text x="40" y="60" text-anchor="middle" font-family="Poppins,sans-serif" font-weight="700" font-size="17" fill="#fff">TAX</text></svg>
    <div class="label">Highest Tax Deductible Contributions Allowed</div>
  </div>

  <div class="hex filled" style="left:464px;top:190px">
    <svg viewBox="0 0 270 270"><polygon points="135,8 250,72 250,198 135,262 20,198 20,72" fill="#0b4a86" stroke="#0b4a86" stroke-width="2.5" stroke-linejoin="round"/></svg>
    <svg class="icon" viewBox="0 0 80 80"><rect x="14" y="6" width="40" height="22" fill="#fff"/><rect x="6" y="30" width="68" height="26" rx="3" fill="#fff"/><text x="40" y="52" text-anchor="middle" font-family="Poppins,sans-serif" font-weight="700" font-size="20" fill="#0b4a86">TAX</text><rect x="14" y="60" width="52" height="6" fill="#fff"/><rect x="14" y="70" width="52" height="5" fill="#fff"/></svg>
    <div class="label">Significantly reduce your taxes</div>
  </div>

  <div class="hex" style="left:790px;top:190px">
    <svg viewBox="0 0 270 270"><polygon points="135,8 250,72 250,198 135,262 20,198 20,72" fill="#fff" stroke="#0b4a86" stroke-width="2.5" stroke-linejoin="round"/></svg>
    <svg class="icon" viewBox="0 0 80 80"><rect x="8" y="48" width="8" height="26" fill="#0b4a86"/><rect x="20" y="38" width="8" height="36" fill="#0b4a86"/><rect x="32" y="20" width="8" height="54" fill="#0b4a86"/><path d="M36 2l12 14h-24z" fill="#0b4a86"/><circle cx="58" cy="42" r="17" fill="none" stroke="#0b4a86" stroke-width="4"/><text x="58" y="50" text-anchor="middle" font-family="Poppins,sans-serif" font-weight="700" font-size="20" fill="#0b4a86">$</text></svg>
    <div class="label">Potential Negative "Net Cost"</div>
  </div>

  <div class="hex" style="left:300px;top:472px">
    <svg viewBox="0 0 270 270"><polygon points="135,8 250,72 250,198 135,262 20,198 20,72" fill="#fff" stroke="#0b4a86" stroke-width="2.5" stroke-linejoin="round"/></svg>
    <svg class="icon" viewBox="0 0 80 80"><circle cx="40" cy="18" r="15" fill="#0b4a86"/><path d="M16 76V48c0-8 6-12 14-12h20c8 0 14 4 14 12v28z" fill="#0b4a86"/><path d="M36 36h8l-4 22z" fill="#fff"/></svg>
    <div class="label">Owner &amp; Executive Weighted Benefits</div>
  </div>

  <div class="hex" style="left:626px;top:472px">
    <svg viewBox="0 0 270 270"><polygon points="135,8 250,72 250,198 135,262 20,198 20,72" fill="#fff" stroke="#0b4a86" stroke-width="2.5" stroke-linejoin="round"/></svg>
    <svg class="icon" viewBox="0 0 80 80"><path d="M40 2v10M22 6l4 8M58 6l-4 8" stroke="#0b4a86" stroke-width="4" stroke-linecap="round"/><path d="M20 22h40l14 16-34 38L6 38z" fill="#0b4a86"/><path d="M6 38h68M30 22l-6 16 16 38M50 22l6 16-16 38" stroke="#fff" stroke-width="2" fill="none"/></svg>
    <div class="label">Retain and Attract Top Talent</div>
  </div>
</section>

<section>
  <h2 class="contrib-title">Allowable Tax-Deductible <span class="accent">Contribution by Age</span></h2>
  <table class="limits">
    <thead><tr>
      <th style="width:143px">Starting Plan at Age:</th>
      <th style="width:143px">Max Monthly Retirement Benefit:</th>
      <th style="width:141px">Lump Sum at Retirement:</th>
      <th style="width:157px">Illustrative Contribution Limits:</th>
      <th style="width:124px">Estimated Tax Savings:</th>
      <th style="width:146px">“Net Cost” after Tax Savings:</th>
    </tr></thead>
    <tbody>
      <tr><td>40</td><td>$20,417</td><td>$2,959,124</td><td>$141,358</td><td>$56,543</td><td>$84,814</td></tr>
      <tr><td>45</td><td>$20,417</td><td>$2,959,124</td><td>$178,753</td><td>$71,501</td><td>$107,252</td></tr>
      <tr><td>50</td><td>$20,417</td><td>$2,959,124</td><td>$246,962</td><td>$98,784</td><td>$148,177</td></tr>
      <tr><td>55</td><td>$20,417</td><td>$2,959,124</td><td>$382,181</td><td>$152,872</td><td>$229,308</td></tr>
      <tr><td>60</td><td>$10,208</td><td>$1,479,561</td><td>$400,418</td><td>$160,192</td><td>$240,225</td></tr>
    </tbody>
  </table>
  <div class="savings-link">How much is your estimated tax savings?</div>
</section>

<section class="amounts">
  <svg class="abs" style="left:0;top:0" width="1200" height="829" viewBox="0 0 1200 829">
    <circle cx="210" cy="340" r="120" fill="none" stroke="#1e78c6" stroke-width="34" opacity=".8"/>
    <circle cx="1030" cy="520" r="150" fill="#0f5aa3" opacity=".7"/>
  </svg>
  <h2 class="sec-title"><b>A Table Of</b> Contribution Amounts</h2>
  <div class="rule" style="top:150px;left:532px;width:136px;background:#fff"></div>
  <svg class="chart" viewBox="0 0 628 370" font-family="Arimo,sans-serif" font-weight="700" font-size="11" fill="#111">
    <text x="50" y="223" text-anchor="middle">Annual</text>
    <text x="50" y="236" text-anchor="middle">Contributio</text>
    <text x="50" y="249" text-anchor="middle">ns</text>
    <text x="50" y="262" text-anchor="middle">Limits</text>
    <rect x="108" y="263" width="50" height="12" fill="#8fcf6b"/>
    <text x="133" y="233" text-anchor="middle">$6,000</text><text x="133" y="247" text-anchor="middle">($7000)</text>
    <text x="133" y="293" text-anchor="middle">IRA</text>
    <rect x="222" y="248" width="50" height="27" fill="#27a33d"/>
    <text x="247" y="218" text-anchor="middle">$20,500</text><text x="247" y="232" text-anchor="middle">($27,000)</text>
    <text x="247" y="293" text-anchor="middle">401(k)</text>
    <rect x="334" y="203" width="52" height="72" fill="#8fbdf0"/>
    <text x="360" y="193" text-anchor="middle">$61,000</text>
    <text x="360" y="293" text-anchor="middle">Profit</text><text x="360" y="306" text-anchor="middle">Sharin</text><text x="360" y="319" text-anchor="middle">g</text>
    <rect x="450" y="85" width="50" height="190" fill="#1f63c9"/>
    <text x="475" y="75" text-anchor="middle">$416,000</text>
    <text x="475" y="293" text-anchor="middle">Cash</text><text x="475" y="306" text-anchor="middle">Balance</text><text x="475" y="319" text-anchor="middle">Plan</text>
    <g font-weight="400" font-size="9.5" text-anchor="middle">
      <text x="570" y="128">"Your</text><text x="570" y="140">contribution</text><text x="570" y="152">limits will be</text>
      <text x="570" y="164">based on age</text><text x="570" y="176">and salary</text><text x="570" y="188">and may not</text>
      <text x="570" y="200">reach the max</text><text x="570" y="212">contribution</text><text x="570" y="224">amount.</text>
    </g>
  </svg>
</section>

<section class="who">
  <div class="abs" style="left:452px;top:3702px;width:135px;height:150px;background:var(--navy);border-radius:8px"></div>
  <div class="who-photo" role="img" aria-label="Photo of a smiling senior woman doctor with glasses and a stethoscope"></div>
  <h2>Who Should Consider <span class="accent">A Cash Balance Plan?</span></h2>
  <p class="intro">You should learn about your options with a Cash Balance Plan design if you are a high earning executive, partner, doctor, or successful business owner and meet the following criteria:</p>
  <ul class="ticks">
    <li style="margin-bottom:26px"><svg width="14" height="14" viewBox="0 0 14 14"><circle cx="7" cy="7" r="7" fill="#14609f"/><path d="M4 7l2 2 4-4" stroke="#fff" stroke-width="1.6" fill="none"/></svg>You are looking to maximize your tax deductions.</li>
    <li style="margin-bottom:26px"><svg width="14" height="14" viewBox="0 0 14 14"><circle cx="7" cy="7" r="7" fill="#14609f"/><path d="M4 7l2 2 4-4" stroke="#fff" stroke-width="1.6" fill="none"/></svg>Your income pushes you beyond the contribution limits of the lower retirement plans such as 401(k)s, SEPs or profit sharing plans.</li>
    <li style="margin-bottom:26px"><svg width="14" height="14" viewBox="0 0 14 14"><circle cx="7" cy="7" r="7" fill="#14609f"/><path d="M4 7l2 2 4-4" stroke="#fff" stroke-width="1.6" fill="none"/></svg>You are in your 40s, 50s, or 60s and don't want the "2nd best" plan.</li>
    <li style="margin-bottom:26px"><svg width="14" height="14" viewBox="0 0 14 14"><circle cx="7" cy="7" r="7" fill="#14609f"/><path d="M4 7l2 2 4-4" stroke="#fff" stroke-width="1.6" fill="none"/></svg>You want an option to GUARANTEE a retirement benefit.</li>
    <li><svg width="14" height="14" viewBox="0 0 14 14"><circle cx="7" cy="7" r="7" fill="#14609f"/><path d="M4 7l2 2 4-4" stroke="#fff" stroke-width="1.6" fill="none"/></svg>You are looking for a way to "catch-up" on retirement savings that provides massive tax savings.</li>
  </ul>
</section>

<section>
  <h2 class="faq-title">Frequently <span class="accent">Asked Questions</span></h2>
  <div class="faq" style="top:4484px;height:58px"><span class="q">What is your company name?</span><span class="plus">+</span></div>
  <div class="faq" style="top:4555px;height:58px"><span class="q">What is your company name?</span><span class="plus">+</span></div>
  <div class="faq" style="top:4626px;height:58px"><span class="q">What is your company name?</span><span class="plus">+</span></div>
  <div class="faq open" style="top:4697px;height:192px"><span class="q">What is your company slogan or mission statement?</span><span class="plus">–</span>
    <p>We help our clients protect their financial futures, build generational wealth, and open doors for the highest allowable tax-deductible contributions for their retirement savings as designed by the federal government. By helping their businesses reduce their tax burden, they're better able to provide for themselves and their employees.</p></div>
  <div class="faq" style="top:4908px;height:58px"><span class="q">What is your company name?</span><span class="plus">+</span></div>
</section>

<footer class="footer">
  <svg class="abs" style="left:0;top:0" width="1200" height="286" viewBox="0 0 1200 286"><path d="M0 14 Q600 -10 1200 14 L1200 286 L0 286Z" fill="#0b4a86"/><rect x="0" y="240" width="1200" height="46" fill="#0a4179"/></svg>
  <div class="f-logo">BrightVale</div>
  <div class="f-links">HOME<span>\</span>ABOUT US<span>\</span>SERVICES<span>\</span>BLOG<span>\</span>CONTACT US</div>
  <div class="copy">© Copyrights 2022 Company name | All Rights reserved</div>
</footer>

</body>
</html>
```